Enrollment Campaign

We need a flyer design for our school's enrollment campaign. Our school website is www.tbvacademy.net.

The flyer should be double sided.

I want the reader to get the following messages:
1. Montessori graduates are leading the top companies of our time.
2. We are an accredited Montessori school.
3. Enrollment is open now for all four programs:
a) Toddler: 18months (or as soon as the child is able to walk) - 3 years
b) CASA: Preschool to Senior Kindergarten (3 years to 6 years)
c) Elementary: Grades 1 to 6
d) Junior High: Grades 7 to 8
4) Our contact information:
website, email:info@tbvacademy.net, phone: 647 382 5146
5) Call for Action: Book a Tour! (there is a button on our website to book a tour)
6) In the languages punjabi, hindi and italian, I wouldn't readers to know that we offer their faith and cultural education as well.
7) Fees for children under age of 6 can be claimed in Taxes as day care expense. So, there is no reason to miss providing our children the best that we can in education.
Updates

Please note my updates to my brief in the "must have" section. Also, I have added some pics that can be used. Please note that I don't have one pic (the farming one referred to in my brief). I will really appreciate if you can kindly update your design accordingly.

Reason: Because of my recent update to the brief, some designers need some time to adjust their designs. I really appreciate your patience and kind consideration for my project. Thank you!

Industry/Entity Type

Education

Colors

Designer to choose colors to be used in the design.

Requirements
Must have
• Must have a unique design. I don't want a typical flyer. The design should be unique and memorable.

One of the main pics that I need is for illustrating a key feature of our new Junior High program that we are starting in August 2015. The key feature is that children are going to be operating a 'greenhouse', growing organic produce and will also be preparing their daily lunch from scratch. So, show a pic of a 13-14year old farming or something.

```html
<!DOCTYPE html>
<html lang="en">
<head>
<meta charset="utf-8">
<title>TBV Academy – Enrollment Flyer</title>
<link rel="stylesheet" href="https://fonts.googleapis.com/css2?family=Mulish:wght@400;600;700;800;900&display=swap">
<style>
  :root {
    --bg: #e4e4e4;
    --paper: #f4f4f2;
    --sky: #29a3dc;
    --sky-light: #4fb9e8;
    --navy: #163e63;
    --navy-mid: #1f6fa8;
    --orange: #ee6d1b;
    --orange-light: #f58a3a;
    --green: #6cb33f;
    --green-light: #8cc95e;
    --ink: #4a4f55;
    --rule: #b9bcbf;
  }
  * { box-sizing: border-box; margin: 0; padding: 0; }
  html, body { width: 847px; height: 1200px; overflow: hidden; background: var(--bg); }
  body { font-family: "Mulish", "Century Gothic", sans-serif; color: var(--ink); position: relative; }

  .sheet { position: absolute; left: 248px; width: 330px; height: 430px; overflow: hidden; }
  .sheet--front { top: 63px; background: #fff; }
  .sheet--back { top: 668px; background: var(--paper); }
  .abs { position: absolute; }
  svg.block { position: absolute; display: block; }

  /* Front */
  .front__title { left: 48px; top: 42px; color: #fff; text-align: right; width: 134px; line-height: 1; font-weight: 800; }
  .front__title .big { font-size: 43px; letter-spacing: -0.5px; display: block; }
  .front__title .mid { font-size: 25px; font-weight: 600; display: block; margin-top: 4px; }
  .front__title .sch { font-size: 29px; display: block; margin-top: 3px; }
  .front__photo { left: 0; top: 169px; width: 330px; height: 261px;
    background: linear-gradient(100deg, #e9b9cf 0%, #f3dbe6 22%, #8db9de 40%, #6a93b8 60%, #86b36a 78%, #d6e2ee 100%); }
  .front__brand { right: 14px; bottom: 12px; color: var(--sky); font-size: 17px; font-weight: 700; }

  /* Back */
  .back__tag { left: 35px; top: 112px; width: 114px; font-size: 8.3px; line-height: 1.4; color: var(--orange); }
  .rule { position: absolute; height: 1px; background: var(--rule); }
  .back__accredited { left: 35px; top: 160px; font-size: 10.5px; line-height: 1.3; color: var(--ink); }
  .back__accredited strong { display: block; font-weight: 800; color: var(--navy); font-size: 10px; letter-spacing: 0.2px; }
  .back__kids { left: 35px; top: 198px; width: 114px; height: 74px;
    background: linear-gradient(120deg, #f2c46b, #e9a0a8 45%, #a9cbe6 80%, #d58fd1); }
  .back__enroll { left: 35px; top: 281px; font-size: 15px; line-height: 1.08; font-weight: 900; color: var(--navy-mid); letter-spacing: 0.2px; }
  .programs { left: 35px; top: 354px; width: 122px; list-style: none; font-size: 5.6px; line-height: 1.35; color: var(--ink); }
  .programs li { position: relative; padding-left: 8px; margin-bottom: 2.5px; }
  .programs li::before { content: ""; position: absolute; left: 0; top: 1.5px; width: 4.5px; height: 4.5px; background: var(--sky); }
  .programs b { color: var(--navy); font-weight: 800; }
  .back__girl { left: 176px; top: 0; width: 142px; height: 157px;
    background: linear-gradient(160deg, #c9a07a, #e8d6c4 40%, #e58ab8 70%, #d9c8b4); }
  .contact__title { left: 176px; top: 209px; font-size: 10.5px; color: var(--orange); font-weight: 600; }
  .contact { left: 176px; top: 228px; list-style: none; font-size: 7.3px; line-height: 1.5; color: var(--ink); }
  .contact li { display: flex; align-items: flex-start; gap: 4px; }
  .contact svg { width: 7px; height: 7px; margin-top: 2px; flex: none; }
  .cta { left: 176px; top: 285px; font-size: 6.8px; line-height: 1.25; }
  .cta strong { font-weight: 800; color: var(--navy); display: block; }
  .cta span { font-size: 5.6px; }
  .note { left: 176px; width: 140px; font-size: 7.2px; line-height: 1.38; }
  .note--faith { top: 315px; color: var(--orange); }
  .note--fees { top: 359px; color: var(--sky); }
  .colorbar { left: 0; bottom: 0; width: 330px; height: 15px; display: flex; }
  .colorbar span { height: 100%; }
</style>
</head>
<body>

<!-- Front side -->
<section class="sheet sheet--front">
  <svg class="block" style="left:0;top:0" width="188" height="163" viewBox="0 0 188 163">
    <rect width="188" height="163" fill="var(--sky)"/>
    <polygon points="0,0 188,163 0,163" fill="var(--sky-light)" opacity="0.45"/>
  </svg>
  <svg class="block" style="left:193px;top:0" width="137" height="97" viewBox="0 0 137 97">
    <rect width="137" height="97" fill="var(--navy)"/>
    <polygon points="0,0 137,0 0,97" fill="var(--navy-mid)"/>
  </svg>
  <svg class="block" style="left:193px;top:103px" width="46" height="60" viewBox="0 0 46 60">
    <rect width="46" height="60" fill="var(--orange)"/>
    <polygon points="46,0 46,60 0,60" fill="var(--orange-light)" opacity="0.6"/>
  </svg>
  <svg class="block" style="left:244px;top:103px" width="86" height="60" viewBox="0 0 86 60">
    <rect width="86" height="60" fill="var(--green)"/>
    <polygon points="0,0 86,60 0,60" fill="var(--green-light)"/>
  </svg>
  <h1 class="abs front__title">
    <span class="big">BACK</span>
    <span class="mid">TO</span>
    <span class="sch">SCHOOL</span>
  </h1>
  <div class="abs front__photo" role="img" aria-label="Photo of a smiling schoolgirl with a pink backpack in front of a school building with flowers"></div>
  <div class="abs front__brand">TBV Academy</div>
</section>

<!-- Back side -->
<section class="sheet sheet--back">
  <svg class="block" style="left:35px;top:0" width="113" height="100" viewBox="0 0 113 100">
    <rect x="0" y="0" width="53" height="47" fill="var(--orange)"/>
    <polygon points="53,0 53,47 0,47" fill="var(--orange-light)" opacity="0.6"/>
    <rect x="59" y="0" width="54" height="47" fill="var(--sky)"/>
    <polygon points="59,0 113,0 113,47" fill="var(--sky-light)" opacity="0.7"/>
    <rect x="0" y="53" width="53" height="47" fill="var(--navy-mid)"/>
    <polygon points="0,100 53,53 53,100" fill="var(--navy)"/>
    <rect x="59" y="53" width="54" height="47" fill="var(--green)"/>
    <polygon points="59,53 113,53 59,100" fill="var(--green-light)"/>
  </svg>
  <div class="rule" style="left:35px;top:108px;width:114px"></div>
  <p class="abs back__tag">Montessori graduates are leading the top companies of our time</p>
  <div class="rule" style="left:35px;top:155px;width:114px"></div>
  <p class="abs back__accredited">We are an accredited <strong>MONTESSORI SCHOOL</strong></p>
  <div class="abs back__kids" role="img" aria-label="Photo of three young children in a colourful classroom"></div>
  <h2 class="abs back__enroll">ENROLLMENT<br>IS OPEN NOW<br>FOR ALL FOUR<br>PROGRAMS</h2>
  <ul class="abs programs">
    <li><b>Toddler</b> 18months (or as soon as the child is able to walk) – 3 years</li>
    <li><b>CASA</b> Preschool to Senior Kindergarten (3 years to 6 years)</li>
    <li><b>Elementary</b> Grades 1 to 6</li>
    <li><b>Junior High</b> Grades 7 to 8</li>
  </ul>

  <div class="abs back__girl" role="img" aria-label="Photo of a girl stacking Montessori cylinder blocks on the floor"></div>
  <div class="rule" style="left:176px;top:203px;width:140px"></div>
  <h3 class="abs contact__title">Our contact information</h3>
  <ul class="abs contact">
    <li><svg viewBox="0 0 10 10"><circle cx="5" cy="5" r="3.6" fill="none" stroke="var(--sky)" stroke-width="1.6"/><circle cx="5" cy="5" r="1.3" fill="var(--sky)"/></svg>www.tbvacademy.net</li>
    <li><svg viewBox="0 0 10 10"><rect x="1" y="2.5" width="8" height="5.5" fill="var(--sky)"/><polyline points="1,2.5 5,6 9,2.5" fill="none" stroke="#fff" stroke-width="0.8"/></svg>info@tbvacademy.net</li>
    <li><svg viewBox="0 0 10 10"><path d="M2.5 1 L4.2 3 L3.2 4.2 Q4.5 6 5.8 6.8 L7 5.8 L9 7.5 L7.8 9 Q3.5 8 1 2.2 Z" fill="var(--sky)"/></svg>647-382-5146</li>
    <li><svg viewBox="0 0 10 10"><polygon points="5,1 9.5,5 8,5 8,9 2,9 2,5 0.5,5" fill="var(--sky)"/></svg>18 Larkfield Crescent<br>Mapleton, ON, L4R 3K9</li>
  </ul>
  <p class="abs cta"><strong>Call for Action: Book a Tour!</strong><span>there is a button on our website to book a tour</span></p>
  <div class="rule" style="left:176px;top:308px;width:140px"></div>
  <p class="abs note note--faith">In the languages punjabi, hindi and italian, I wouldn't readers to know that we offer their faith and cultural education as well.</p>
  <p class="abs note note--fees">Fees for children under age of 6 can be claimed in Taxes as day care expense. So, there is no reason to miss providing our children the best that we can in education.</p>

  <div class="abs colorbar">
    <span style="width:68px;background:var(--sky)"></span>
    <span style="width:20px;background:var(--orange)"></span>
    <span style="width:45px;background:var(--green)"></span>
    <span style="width:86px;background:var(--navy-mid)"></span>
    <span style="width:111px;background:var(--navy)"></span>
  </div>
</section>

</body>
</html>
```